Retail/Wholesale website graphic template

I need to design a new graphic template for a website for a client. The website will be a retail/wholesale company site with most pages dedicated to presentation. There will also be an online store and a blog. However, you don't need to worry about those. All I need from you is a graphic template for a generic site page.

It will need to include standard UI elements, in case I need those. I am attaching a more detailed assignment in .docx format.

The logo is also attached.

Target Market(s)

small business owners, (occasional) retail customers

Industry/Entity Type

Wholesale

Number of Pages Required

1 page

Font styles to use
Serif
Sans Serif

Colors
ec1f27
474747

Requirements
Must have
• must match logo, be clean, minimal and with slightly larger text size
Should not have
• must not be modern-looking where you have to scroll and scroll and scroll to get to the bottom of the homepage. most of my visitors are "old" people, they do not get this type of design.

```html
<!DOCTYPE html>
<html lang="en">
<head>
<meta charset="utf-8">
<title>Larkfield Trading</title>
<link href="https://fonts.googleapis.com/css2?family=Montserrat:wght@500;600;700;800&family=Open+Sans:wght@400;600&display=swap" rel="stylesheet">
<style>
:root{
  --red:#e31e2b;
  --dark:#3b3b3b;
  --darker:#2f2f2f;
  --footer:#333333;
  --ink:#1e1e1e;
  --body:#555555;
  --light:#f2efef;
  --white:#ffffff;
  --line:#dddddd;
}
*{margin:0;padding:0;box-sizing:border-box}
html,body{width:1200px;height:2922px;overflow:hidden}
body{position:relative;background:var(--white);font-family:"Open Sans",Arial,sans-serif;color:var(--body)}
.abs{position:absolute}
.heading{font-family:"Montserrat",Arial,sans-serif;font-weight:700;color:var(--ink)}
.btn{position:absolute;display:flex;align-items:center;justify-content:center;background:var(--red);color:var(--white);font-family:"Montserrat",Arial,sans-serif;font-weight:700;font-size:12px;letter-spacing:.3px;text-transform:uppercase;white-space:nowrap}
.btn.inverse{background:var(--white);color:var(--red)}

/* top bar */
.topbar{left:0;top:0;width:1200px;height:30px;background:var(--darker);color:var(--white);font-size:11px;font-weight:600}
.topbar .item{position:absolute;top:8px;display:flex;align-items:center;gap:8px;white-space:nowrap}
.topbar .sep{position:absolute;top:6px;width:1px;height:18px;background:#555}

/* header */
.brand{left:127px;top:18px;width:300px;height:99px;display:flex;align-items:center;gap:12px;white-space:nowrap}
.brand i{width:18px;height:18px;background:var(--red);display:block;flex:none}
.brand span{font-family:"Montserrat",Arial,sans-serif;font-weight:700;font-size:27px;color:var(--ink)}
.nav{top:76px;font-family:"Montserrat",Arial,sans-serif;font-weight:700;font-size:11.5px;color:var(--ink);white-space:nowrap}
.nav.active{top:72px;left:800px;width:77px;height:23px;background:var(--red);color:var(--white);display:flex;align-items:center;justify-content:center}
.dropdown{left:800px;top:95px;width:155px;height:158px;background:var(--red);z-index:4;padding:25px 0 0 30px}
.dropdown li{list-style:none;font-family:"Montserrat",Arial,sans-serif;font-weight:700;font-size:11px;color:var(--white);text-transform:uppercase;height:28px}

/* hero */
.hero{left:0;top:136px;width:1200px;height:536px;background:linear-gradient(180deg,#6b7686 0%,#8f8f94 45%,#5c5f66 100%)}
.hero-title{left:0;top:344px;width:1200px;text-align:center;font-family:"Montserrat",Arial,sans-serif;font-weight:800;font-size:40px;color:var(--white);text-transform:uppercase}
.dots{left:540px;top:604px;display:flex;gap:13px}
.dots i{width:10px;height:10px;border-radius:50%;background:var(--white);display:block}
.dots i.on{background:var(--red);box-shadow:0 0 0 2px var(--white)}

/* welcome */
.welcome{left:130px;top:727px;width:612px;height:362px;background:linear-gradient(160deg,#3f77c4 0%,#7ea4cf 45%,#3d5668 80%,#2d4a2b 100%)}
.welcome-title{left:170px;top:938px;font-family:"Montserrat",Arial,sans-serif;font-weight:800;font-size:24px;color:var(--white);text-transform:uppercase}
.welcome-text{left:170px;top:971px;width:390px;font-size:12px;line-height:15px;color:var(--white)}
.offer{left:756px;top:727px;width:313px;height:362px;background:var(--dark);padding:34px 0 0 27px}
.offer h3{font-family:"Montserrat",Arial,sans-serif;font-weight:700;font-size:15px;color:var(--white);text-transform:uppercase;margin-bottom:20px}
.offer li{list-style:none;font-size:13px;color:var(--white);height:26.5px;display:flex;align-items:center;gap:12px}
.offer li::before{content:"";border-left:5px solid var(--white);border-top:4px solid transparent;border-bottom:4px solid transparent}

/* service cards */
.card{top:1120px;width:295px;height:306px;background:var(--dark);text-align:center;color:var(--white)}
.card.featured{background:var(--red)}
.card svg{position:absolute;left:122px;top:40px}
.card h4{position:absolute;top:118px;width:100%;font-family:"Montserrat",Arial,sans-serif;font-weight:800;font-size:20px;text-transform:uppercase}
.card p{position:absolute;top:162px;left:45px;width:205px;font-size:12px;line-height:15px;color:#e6e6e6}
.card .btn{left:100px;top:249px;width:95px;height:28px}

/* about band */
.band{left:0;top:1500px;width:1200px;height:405px;background:var(--light)}
.about-title{left:132px;top:1590px;font-size:17px;line-height:31px;text-transform:uppercase;white-space:nowrap}
.about-text{left:132px;top:1668px;width:486px;font-size:12.3px;line-height:14.3px;text-align:justify;color:#444}
.feature{left:746px;width:316px;height:68px;background:var(--white);border:1px solid var(--line);box-shadow:0 1px 3px rgba(0,0,0,.08)}
.feature .ico{position:absolute;left:22px;top:13px;width:42px;height:42px;border-radius:50%;background:var(--dark);display:flex;align-items:center;justify-content:center}
.feature .rule{position:absolute;left:94px;top:16px;width:1px;height:36px;background:#ccc}
.feature b{position:absolute;left:124px;top:18px;font-family:"Montserrat",Arial,sans-serif;font-size:13px;color:var(--ink)}
.feature span{position:absolute;left:124px;top:38px;font-size:11px;color:#666}

/* blog */
.blog-title{left:0;top:1988px;width:1200px;text-align:center;font-size:22px;text-transform:uppercase}
.blog-rule{left:576px;top:2034px;width:48px;height:3px;background:#cfcfcf}
.post{top:2106px;width:265px;height:358px;background:var(--white);border:1px solid var(--line)}
.post .photo{position:absolute;left:13px;top:13px;width:240px;height:158px}
.post h5{position:absolute;left:26px;top:194px;width:220px;font-family:"Montserrat",Arial,sans-serif;font-weight:700;font-size:13px;line-height:17px;color:var(--ink)}
.post p{position:absolute;left:26px;top:243px;width:215px;font-size:11px;line-height:14px;color:#555}
.post a{position:absolute;left:26px;top:317px;font-family:"Montserrat",Arial,sans-serif;font-weight:700;font-size:10.5px;color:var(--red);text-decoration:none}

/* footer */
.footer{left:0;top:2552px;width:1200px;height:370px;background:var(--footer);color:#e5e5e5}
.footer-brand{left:130px;top:2622px;width:290px;height:92px;display:flex;align-items:center;gap:12px;white-space:nowrap}
.footer-brand i{width:18px;height:18px;background:var(--white);display:block;flex:none}
.footer-brand span{font-family:"Montserrat",Arial,sans-serif;font-weight:700;font-size:27px;color:var(--white)}
.foot-head{top:2616px;font-family:"Montserrat",Arial,sans-serif;font-weight:700;font-size:12px;color:var(--white);text-transform:uppercase;white-space:nowrap}
.foot-list{font-size:11.5px;line-height:17.5px;color:#dcdcdc;list-style:none}
.contact-row{left:495px;display:flex;gap:14px;font-size:11.5px;line-height:17px;color:#dcdcdc}
.social{left:955px;display:flex;align-items:center;gap:12px;font-size:11.5px;color:#dcdcdc}
.social i{width:26px;height:26px;border-radius:50%;display:block}
.foot-rule{left:130px;top:2830px;width:940px;height:1px;background:#4a4a4a}
.copyright{left:0;top:2877px;width:1200px;text-align:center;font-size:11px;color:#dcdcdc}
</style>
</head>
<body>

<!-- top bar -->
<div class="abs topbar">
  <div class="item" style="left:700px">
    <svg width="11" height="11" viewBox="0 0 24 24"><path fill="#fff" d="M6.6 10.8a15 15 0 0 0 6.6 6.6l2.2-2.2a1 1 0 0 1 1-.25 11.4 11.4 0 0 0 3.6.57 1 1 0 0 1 1 1V20a1 1 0 0 1-1 1A17 17 0 0 1 3 4a1 1 0 0 1 1-1h3.5a1 1 0 0 1 1 1c0 1.25.2 2.45.57 3.57a1 1 0 0 1-.25 1z"/></svg>
    555.010.2040
  </div>
  <div class="sep" style="left:805px"></div>
  <div class="item" style="left:822px">
    <svg width="12" height="10" viewBox="0 0 24 18"><path fill="#fff" d="M0 0h24v18H0zM2 2v1l10 7 10-7V2z"/></svg>
    info@larkfieldtrading.com
  </div>
  <div class="sep" style="left:993px"></div>
  <div class="item" style="left:1013px">
    <svg width="9" height="11" viewBox="0 0 18 22"><path fill="#fff" d="M3 9V6a6 6 0 0 1 12 0v3h3v13H0V9zm3 0h6V6a3 3 0 0 0-6 0z"/></svg>
    Login
  </div>
</div>

<!-- header -->
<div class="abs brand"><i></i><span>Larkfield Trading</span></div>
<div class="abs nav" style="left:620px">HOME</div>
<div class="abs nav" style="left:703px">ABOUT US</div>
<div class="abs nav active">SERVICES</div>
<div class="abs nav" style="left:923px">BLOG</div>
<div class="abs nav" style="left:995px">CONTACT US</div>
<ul class="abs dropdown">
  <li>Retail</li><li>Wholesale</li><li>Import</li><li>Lorem ipsum</li>
</ul>

<!-- hero -->
<div class="abs hero" role="img" aria-label="Warehouse aisle with tall shelves stocked with boxed retail goods"></div>
<div class="abs hero-title">Whole Sale Import</div>
<div class="btn" style="left:526px;top:420px;width:146px;height:40px;font-size:15px">Read more</div>
<div class="abs dots"><i></i><i></i><i class="on"></i><i></i><i></i></div>

<!-- welcome + offer -->
<div class="abs welcome" role="img" aria-label="Modern glass office building under a blue sky"></div>
<div class="abs welcome-title">Welcome to our site</div>
<div class="abs welcome-text">Sed ut perspiciatis unde omnis iste natus error sit voluptatem accusantium doloremque laudantium, totam rem aperiam, eaque ipsa quae ab illo inventore veritatis</div>
<div class="btn" style="left:172px;top:1037px;width:91px;height:28px">Read more</div>

<div class="abs offer">
  <h3>Lorem ipsum is simpl</h3>
  <ul>
    <li>Bulk wholesale</li>
    <li>Custom clearance</li>
    <li>Logistic support</li>
    <li>Marketing consultation</li>
    <li>Product labeling</li>
    <li>Drop shipping</li>
    <li>Spa, Barber &amp; Beauty Supplies</li>
  </ul>
</div>
<div class="btn" style="left:789px;top:1027px;width:91px;height:28px">Read more</div>

<!-- service cards -->
<div class="abs card" style="left:130px">
  <svg width="52" height="50" viewBox="0 0 52 50"><path d="M2 4h8l7 28h26l6-20H13" fill="none" stroke="#fff" stroke-width="4" stroke-linejoin="round"/><path d="M18 18h28M20 25h24" stroke="#fff" stroke-width="3"/><circle cx="20" cy="42" r="4" fill="#fff"/><circle cx="40" cy="42" r="4" fill="#fff"/></svg>
  <h4>Retail</h4>
  <p>Sed ut perspiciatis unde omnis iste natus error sit voluptatem accus antium doloremque lau architecto beatae vitae dicta sunt exp</p>
  <div class="btn">Read more</div>
</div>
<div class="abs card featured" style="left:454px">
  <svg width="52" height="50" viewBox="0 0 52 50"><rect x="3" y="6" width="46" height="38" fill="none" stroke="#fff" stroke-width="4"/><path d="M14 12v26M22 12v26M30 12v26M38 12v26" stroke="#fff" stroke-width="3"/></svg>
  <h4>Import</h4>
  <p>Sed ut perspiciatis unde omnis iste natus error sit voluptatem accus antium doloremque lau architecto beatae vitae dicta sunt exp</p>
  <div class="btn inverse">Read more</div>
</div>
<div class="abs card" style="left:773px">
  <svg width="52" height="50" viewBox="0 0 52 50"><path d="M3 18 26 4l23 14v28H3z" fill="none" stroke="#fff" stroke-width="4" stroke-linejoin="round"/><path d="M12 22h28v24M12 22v24M12 29h28M12 36h28" fill="none" stroke="#fff" stroke-width="3"/></svg>
  <h4>Whole sale</h4>
  <p>Sed ut perspiciatis unde omnis iste natus error sit voluptatem accus antium doloremque lau architecto beatae vitae dicta sunt exp</p>
  <div class="btn">Read more</div>
</div>

<!-- about band -->
<div class="abs band"></div>
<div class="abs heading about-title">Lorem ipsum dolor sit amet consecte<br>adipiscing elit&nbsp; sed do</div>
<p class="abs about-text">But I must explain to you how all this mistaken idea of denouncing pleasure and praising pain was born and I will give you a complete account of the system, and expound the actual teachings of the great explorer of the truth, the master-builder of human happiness. No one rejects, dislikes, or avoids pleasure itself, because it is pleasure, but because those who do not know how to pursue pleasure rationally encounter consequences that are extremely painful. Nor again is there anyone who loves or pursues or desires to obtain pain of itself, because it is pain, but because occasionally circumsta who do not know how to pursue pleasure rationally encounter consequences that are extremely painful. Nor again is there anyone who loves or pursues or desires to obtain pain of itself, because it is pain.</p>

<div class="abs feature" style="top:1586px">
  <div class="ico"><svg width="24" height="18" viewBox="0 0 24 18"><path fill="#fff" d="M0 1h14v11H0zM15 5h5l4 4v3h-9z"/><circle cx="5" cy="15" r="2.5" fill="#fff"/><circle cx="19" cy="15" r="2.5" fill="#fff"/></svg></div>
  <div class="rule"></div><b>Shipping low</b><span>Shipping low cost</span>
</div>
<div class="abs feature" style="top:1669px">
  <div class="ico"><svg width="16" height="16" viewBox="0 0 24 24"><path fill="#fff" d="M6.6 10.8a15 15 0 0 0 6.6 6.6l2.2-2.2a1 1 0 0 1 1-.25 11.4 11.4 0 0 0 3.6.57 1 1 0 0 1 1 1V20a1 1 0 0 1-1 1A17 17 0 0 1 3 4a1 1 0 0 1 1-1h3.5a1 1 0 0 1 1 1c0 1.25.2 2.45.57 3.57a1 1 0 0 1-.25 1z"/></svg></div>
  <div class="rule"></div><b>Call Us</b><span>Denouncing pleasure</span>
</div>
<div class="abs feature" style="top:1755px">
  <div class="ico"><span style="position:static;font-family:Montserrat,Arial,sans-serif;font-weight:700;font-size:20px;color:#fff">$</span></div>
  <div class="rule"></div><b>Wholesale prices</b><span>Wholesale...</span>
</div>

<!-- blog -->
<div class="abs heading blog-title">Latest blog</div>
<div class="abs blog-rule"></div>

<div class="abs post" style="left:166px">
  <div class="photo" role="img" aria-label="Store aisle lined with packaged groceries" style="background:linear-gradient(135deg,#c9413a,#d8b35a 50%,#4d6aa0)"></div>
  <h5>Lorem ipsum dolor sit amet consectetur adipiscin</h5>
  <p>Sed ut perspiciatis unde omnis iste natus error sit voluptatem accusantium doloremque laudantium totam rem aperiam, eaque ipsa qua.</p>
  <a>READ MORE &rsaquo;</a>
</div>
<div class="abs post" style="left:468px">
  <div class="photo" role="img" aria-label="Brick storefront building with a rounded glass entrance" style="background:linear-gradient(180deg,#3f7fd0 0%,#9fbfe6 35%,#a45a45 60%,#7c7c7c 100%)"></div>
  <h5>Lorem ipsum dolor sit amet consectetur adipiscin</h5>
  <p>Sed ut perspiciatis unde omnis iste natus error sit voluptatem accusantium doloremque laudantium totam rem aperiam, eaque ipsa qua.</p>
  <a>READ MORE &rsaquo;</a>
</div>
<div class="abs post" style="left:771px">
  <div class="photo" role="img" aria-label="Warehouse racks stacked with cardboard boxes" style="background:linear-gradient(135deg,#b47a4c,#d9b98c 50%,#5a5f6b)"></div>
  <h5>Lorem ipsum dolor sit amet consectetur adipiscin</h5>
  <p>Sed ut perspiciatis unde omnis iste natus error sit voluptatem accusantium doloremque laudantium totam rem aperiam, eaque ipsa qua.</p>
  <a>READ MORE &rsaquo;</a>
</div>

<!-- footer -->
<div class="abs footer"></div>
<div class="abs footer-brand"><i></i><span>Larkfield Trading</span></div>

<div class="abs foot-head" style="left:495px">Contact us</div>
<div class="abs contact-row" style="top:2650px">
  <svg width="11" height="15" viewBox="0 0 12 16" style="margin-top:2px"><path fill="#fff" d="M6 0a6 6 0 0 1 6 6c0 4.5-6 10-6 10S0 10.5 0 6a6 6 0 0 1 6-6zm0 3.5a2.5 2.5 0 1 0 0 5 2.5 2.5 0 0 0 0-5z"/></svg>
  <div>78 Depot Lane<br>Millbrook, IL 60400</div>
</div>
<div class="abs contact-row" style="top:2698px">
  <svg width="11" height="11" viewBox="0 0 24 24" style="margin-top:3px"><path fill="#fff" d="M6.6 10.8a15 15 0 0 0 6.6 6.6l2.2-2.2a1 1 0 0 1 1-.25 11.4 11.4 0 0 0 3.6.57 1 1 0 0 1 1 1V20a1 1 0 0 1-1 1A17 17 0 0 1 3 4a1 1 0 0 1 1-1h3.5a1 1 0 0 1 1 1c0 1.25.2 2.45.57 3.57a1 1 0 0 1-.25 1z"/></svg>
  <div>555.010.2040</div>
</div>
<div class="abs contact-row" style="top:2737px">
  <svg width="12" height="10" viewBox="0 0 24 18" style="margin-top:4px"><path fill="#fff" d="M0 0h24v18H0zM2 2v1l10 7 10-7V2z"/></svg>
  <div>info@larkfield.com</div>
</div>

<div class="abs foot-head" style="left:752px">Menu</div>
<ul class="abs foot-list" style="left:752px;top:2648px">
  <li>Home</li><li>About Us</li><li>Services</li><li>Blog</li><li>Our Process</li><li>Contact us</li>
</ul>

<div class="abs foot-head" style="left:955px">Connect with us</div>
<div class="abs social" style="top:2650px"><i style="background:#3b5a9a"></i>Community</div>
<div class="abs social" style="top:2691px"><i style="background:#2aa3e0"></i>Updates</div>
<div class="abs social" style="top:2731px"><i style="background:#1d2f6b"></i>Network</div>

<div class="abs foot-rule"></div>
<div class="abs copyright">XML site&nbsp; |&nbsp; privacy policy&nbsp; |&nbsp; Copyrights @ 2018 All Rights Reserved</div>

</body>
</html>
```